Popup Nightclub Grand Opening Flyer

We need to design a flyer for the grand opening of an upscale, exclusive nightclub called "Lantern". The design needs to be chic and exclusive. The background should be black and the text should primarily be white. We like minimalist designs.

Here is the text for the flyer
-
Velvetroll Atlanta Presents

Lantern (LOGO)

A Popup Nightclub Experience
For one night Only

Friday, October 18, 2013
Party begins at 9PM

INVITE ONLY

See invitation for location details
(Velvetroll Atlanta logo)

-
Examples we like

http://cdn4-x.pressfolio-example.com/sites/default/files/styles/image_content_width/hash/3b/fd/2468013579_4421_flyer.jpg?itok=K9rtQw2z

http://files.hubspace-example.net/files/8Hqq-Tr72WWE3kaRbTmcxP5QZK2F396J8nbRw4CKMHfdX2Y7qSEF-MqjxDoNrLY3QCyQJD7npjGaRq3k-Mhx6hqf3MDSWf8r3/2zenSaturdays.jpg

http://morvex-example.com/wp-content/uploads/siteskin/widgetkit/gallery/2zen/2zen-gen_qstay4-01.jpg

Hi All, one thing that we are seeing that we don't like is on over emphasis on the phrase "a popup nightclub experience" please don't make this the largest thing on the flyer

Target Market(s)

Target market is 25-35 year olds who are affluent (rich) and like luxury brands

Requirements
Must have
• Dark Background
Nice to have
• Velvetroll Logo on the bottom
Modern text that isn't curvy
Should not have
• Curved text

```html
<!DOCTYPE html>
<html lang="en">
<head>
<meta charset="utf-8">
<title>Lantern Nightclub – Popup Flyer</title>
<link rel="stylesheet" href="https://fonts.googleapis.com/css2?family=Jost:wght@300&family=Share+Tech+Mono&display=swap">
<style>
  :root {
    --page-bg: #e9e9e9;
    --flyer-bg: #0d0d0d;
    --photo-tone-light: #2a2a2a;
    --photo-tone-dark: #080808;
    --text-white: #ffffff;
    --text-grey: #a9a9a9;
    --text-soft: #c4c4c4;
  }
  html, body {
    margin: 0;
    width: 1200px;
    height: 1000px;
    overflow: hidden;
    background: var(--page-bg);
  }
  .flyer {
    position: absolute;
    left: 282px;
    top: 18px;
    width: 678px;
    height: 962px;
    background: var(--flyer-bg);
    overflow: hidden;
    color: var(--text-white);
    font-family: "Share Tech Mono", monospace;
  }
  .flyer__photo {
    position: absolute;
    inset: 0;
    background:
      radial-gradient(ellipse 42% 48% at 72% 38%, var(--photo-tone-light), transparent 70%),
      radial-gradient(ellipse 30% 30% at 40% 62%, #1c1c1c, transparent 70%),
      linear-gradient(160deg, #161616, var(--photo-tone-dark));
  }
  .line {
    position: absolute;
    left: 0;
    width: 100%;
    margin: 0;
    text-align: center;
    font-variant: small-caps;
    white-space: nowrap;
  }
  .presenter { top: 56px; font-size: 21px; letter-spacing: 3px; color: var(--text-soft); }
  .brand-mark {
    position: absolute;
    left: 50%;
    top: 132px;
    width: 150px;
    height: 150px;
    margin-left: -75px;
  }
  .brand-name {
    top: 340px;
    font-family: "Jost", sans-serif;
    font-weight: 300;
    font-size: 68px;
    letter-spacing: 12px;
    padding-left: 12px;
    box-sizing: border-box;
    font-variant: normal;
    color: var(--text-white);
  }
  .brand-sub {
    top: 424px;
    font-family: "Jost", sans-serif;
    font-weight: 300;
    font-size: 35px;
    letter-spacing: 5px;
    font-variant: normal;
    color: var(--text-white);
  }
  .tagline { top: 572px; font-size: 23px; letter-spacing: 3px; }
  .tagline-sub { top: 602px; font-size: 21px; letter-spacing: 3px; color: var(--text-grey); }
  .date { top: 662px; font-size: 23px; letter-spacing: 3px; }
  .time { top: 692px; font-size: 21px; letter-spacing: 3px; color: var(--text-grey); }
  .access { top: 766px; font-size: 23px; letter-spacing: 3px; }
  .location-note { top: 846px; font-size: 21px; letter-spacing: 3px; color: var(--text-grey); }
  .host {
    position: absolute;
    left: 0;
    width: 100%;
    top: 902px;
    display: flex;
    justify-content: center;
    align-items: center;
    gap: 12px;
  }
  .host__dot {
    width: 26px;
    height: 26px;
    border-radius: 50%;
    border: 2px solid var(--text-white);
    box-sizing: border-box;
  }
  .host__name {
    font-size: 24px;
    letter-spacing: 2px;
    color: var(--text-white);
  }
</style>
</head>
<body>
  <main class="flyer">
    <div class="flyer__photo" role="img" aria-label="Faint dark black-and-white photograph of a dancing clubgoer behind the text"></div>

    <p class="line presenter">Velvetroll Atlanta Presents</p>

    <svg class="brand-mark" viewBox="0 0 150 150" aria-hidden="true">
      <circle cx="75" cy="75" r="72" fill="none" stroke="#cfcfcf" stroke-width="4"/>
    </svg>
    <h1 class="line brand-name">LANTERN</h1>
    <p class="line brand-sub">NIGHTCLUB</p>

    <p class="line tagline">A Popup Nightclub Experience</p>
    <p class="line tagline-sub">For one night Only</p>

    <p class="line date">Friday, October 18, 2013</p>
    <p class="line time">Party begins at 9PM</p>

    <p class="line access">INVITE ONLY</p>

    <p class="line location-note">See invitation for location details</p>

    <div class="host">
      <span class="host__dot" aria-hidden="true"></span>
      <span class="host__name">VELVETROLL ATLANTA</span>
    </div>
  </main>
</body>
</html>
```